Sophisticated, clean website reflecting my feminine, playful side to sell my abstract art,

I need a website no more than 3 pages to showcase my paintings, a little about me and some contact info. I do abstracts so looking for something a little edgy, yet feminine and current.
Updates

Hi there, These are some artists websites that I Iike: Marnelvoss.com (I like how airy it is) peterwallombry.com garethpolvens.com (I like how it scrolls) I'll need a place for a photo ( a headshot-i do not have it yet so I'll need to be able to upload that later) as well as an area for my bio. Also, it's important that I will be able to upload any new photos and descriptions easily so it should be user friendly. Lastly, I like in a sunny place so would like to have this seem upbeat and playful as that is how i like to paint. thanks-I'm trying to upload my photos now -

Target Market(s)

ppl ages 35-70 who want large scale art for their homes

Industry/Entity Type

art

Coding

Coded - Design and coding required

Number of Pages Required

3 page

Colors

Designer to choose colors to be used in the design.

Requirements
Must have
• photos of my art, a place for my bio, be easy to reach me. tasteful-nothing too "in your face" -my clients are pretty high end and organized. They like clean lines
Nice to have
• sophisticated background, muted tones in the back-similar clean font throughout-no cursive
Should not have
• too many dark areas. Too many blocks of color. Too serious.

```html
<!DOCTYPE html>
<html lang="en">
<head>
<meta charset="utf-8">
<title>Artist Gallery</title>
<link rel="stylesheet" href="https://fonts.googleapis.com/css2?family=Cinzel:wght@400;600&family=Montserrat:wght@400;500&family=Raleway:wght@400&display=swap">
<style>
:root{
  --ink:#111111;
  --cream:#fdf3e3;
  --frame:#e6e6e6;
  --rule:#bdbdbd;
  --butter:#e9dc8e;
  --caption:rgba(236,226,160,0.85);
  --dot:#e5d680;
  --arrow-bg:rgba(40,40,40,0.55);
  --muted:#444444;
}
*{box-sizing:border-box;margin:0;padding:0}
html,body{width:1200px;height:2161px;overflow:hidden;background:#fff}
body{position:relative;font-family:"Montserrat",sans-serif;color:var(--ink)}
.site-logo{position:absolute;left:545px;top:17px;width:110px;height:26px;border:1px solid var(--ink);font:500 14px/24px "Montserrat",sans-serif;text-align:center;letter-spacing:.2px}
.main-nav{position:absolute;left:0;top:62px;width:1200px;height:44px;background:var(--cream)}
.main-nav a{position:absolute;top:13px;font-size:14.5px;color:var(--ink);text-decoration:none;white-space:nowrap}
.main-nav a.is-active{top:9px;padding:2px 7px;border:1px solid var(--ink);border-radius:2px}
.hero{position:absolute;left:0;top:106px;width:1200px;height:636px;
  background:radial-gradient(circle at 72% 48%,#e8c45a 0,#d9a82a 14%,rgba(233,230,222,0) 32%),
  radial-gradient(circle at 12% 62%,#d98a3a 0,#c9a030 14%,rgba(233,230,222,0) 30%),
  radial-gradient(circle at 55% 20%,#2f5ea8 0,rgba(233,230,222,0) 22%),
  linear-gradient(135deg,#e9e6de,#ece8df 50%,#e3ddd0)}
.hero-arrow{position:absolute;top:411px;width:40px;height:40px;background:var(--arrow-bg)}
.hero-arrow.prev{left:0}.hero-arrow.next{right:0}
.hero-arrow svg{display:block;margin:12px auto}
.feature{position:absolute;left:164px;top:839px;width:873px;height:491px;border:3px solid #fff;box-shadow:0 0 4px rgba(0,0,0,.35)}
.feature-art{position:absolute;inset:0;background:linear-gradient(100deg,#9aa3bd 0%,#5f9a98 45%,#27706f 65%,#2d3f6e 100%)}
.feature-caption{position:absolute;left:0;right:0;bottom:0;height:63px;background:var(--caption);font:600 40px/63px "Cinzel",serif;text-align:center;color:var(--ink);white-space:nowrap}
.feature-btn{position:absolute;top:1219px;width:36px;height:26px}
.feature-btn.prev{left:990px;background:#fff}
.feature-btn.next{left:1045px;background:var(--butter)}
.feature-btn svg{display:block;margin:7px auto}
.section-title{position:absolute;left:0;width:1200px;top:1436px;font:600 44px/56px "Cinzel",serif;text-align:center}
.title-rule{position:absolute;left:530px;top:1497px;width:140px;height:1px;background:var(--rule)}
.title-rule::after{content:"";position:absolute;left:63px;top:-1px;width:14px;height:2px;background:var(--ink)}
.portfolio-frame{position:absolute;left:411px;top:1559px;width:225px;height:329px;border:13px solid var(--frame)}
.portfolio-art{position:absolute;left:463px;top:1608px;width:324px;height:378px;box-shadow:0 1px 4px rgba(0,0,0,.25);
  background:radial-gradient(circle at 55% 50%,#e3b94a 0,#d4a12a 35%,#c88a2b 55%,#e8e2d4 85%)}
.pager{position:absolute;top:1765px;font:400 13px/16px "Raleway",sans-serif;color:var(--muted)}
.pager .line{position:absolute;top:8px;width:44px;height:1px;background:#999}
.pager.prev{left:248px}.pager.prev .line{left:46px}
.pager.next{left:926px}.pager.next .line{left:-64px}
.dots{position:absolute;top:2025px;left:577px;height:10px}
.dots span{position:absolute;top:2px;width:6px;height:6px;border-radius:50%;background:var(--dot)}
.dots span.is-current{top:-1px;width:12px;height:12px;background:#fff;border:1px solid var(--ink)}
.dots span.is-current::after{content:"";position:absolute;left:2px;top:2px;width:6px;height:6px;border-radius:50%;background:var(--ink)}
.footer-nav a{position:absolute;top:2097px;font:400 15px/20px "Raleway",sans-serif;color:var(--ink);text-decoration:none}
.social{position:absolute;top:2100px;right:161px;font:400 10px/14px "Raleway",sans-serif;color:var(--ink)}
.social span{margin-left:10px}
.footer-rule{position:absolute;left:163px;top:2125px;width:876px;height:1px;background:#cfcfcf}
.copyright{position:absolute;left:0;width:1200px;top:2137px;font:400 11px/14px "Raleway",sans-serif;text-align:center;color:#333}
</style>
</head>
<body>
<header>
  <div class="site-logo">ARTIST LOGO</div>
  <nav class="main-nav">
    <a class="is-active" href="#" style="left:163px">Originals For Sale</a>
    <a href="#" style="left:394px">Print For Sale</a>
    <a href="#" style="left:591px">Events</a>
    <a href="#" style="left:741px">Past Work</a>
    <a href="#" style="left:917px">About The Artist</a>
  </nav>
</header>

<section class="hero" role="img" aria-label="Featured abstract painting in warm ochre, blue and orange tones">
  <span class="hero-arrow prev"><svg width="12" height="16" viewBox="0 0 12 16"><path d="M11 1 2 8l9 7z" fill="#e8e8e8"/></svg></span>
  <span class="hero-arrow next"><svg width="12" height="16" viewBox="0 0 12 16"><path d="M1 1l9 7-9 7z" fill="#e8e8e8"/></svg></span>
</section>

<section class="feature">
  <div class="feature-art" role="img" aria-label="Featured abstract painting in cool lavender, teal and navy tones"></div>
  <div class="feature-caption">Create Your Own Galery Today!</div>
</section>
<span class="feature-btn prev"><svg width="10" height="12" viewBox="0 0 10 12"><path d="M9 0 0 6l9 6z" fill="#111"/></svg></span>
<span class="feature-btn next"><svg width="10" height="12" viewBox="0 0 10 12"><path d="M1 0l9 6-9 6z" fill="#fff"/></svg></span>

<h2 class="section-title">Our Portfolio</h2>
<div class="title-rule"></div>

<div class="portfolio-frame"></div>
<div class="portfolio-art" role="img" aria-label="Portfolio abstract painting in golden ochre tones"></div>
<div class="pager prev">PREV<span class="line"></span></div>
<div class="pager next"><span class="line"></span>NEXT</div>
<div class="dots">
  <span style="left:0"></span><span style="left:13px"></span><span class="is-current" style="left:24px"></span><span style="left:42px"></span>
</div>

<footer>
  <nav class="footer-nav">
    <a href="#" style="left:163px">Our Beauty</a>
    <a href="#" style="left:277px">Fashion</a>
    <a href="#" style="left:367px">Men</a>
    <a href="#" style="left:433px">Special</a>
    <a href="#" style="left:519px">Wedding</a>
  </nav>
  <div class="social"><span>Plusly</span><span>Pictogram</span></div>
  <div class="footer-rule"></div>
  <p class="copyright">Copyright © 2022. All rights reserved.</p>
</footer>
</body>
</html>
```